Business Card Design Project

- makeup artist business card

- original and creative

- Elegant design

- Feel free to come out with cool designs but stick to being elegant and attractive

- Design relates to makeup

- includes name, occupation, contact numbers, email, website

- regular size business card

- round corner card

- double sided

- on 1 side it should just have the website name in the center " moonveilstudio.net "

Industry/Entity Type

Business

Requirements
Must have
• Delia Marsh
Makeup Artist
USA: +1 (415)772-0461
Singapore: +65 82307915
deliamarsh@moonveilstudio.net
www.moonveilstudio.net
Should not have
• nothing cartoon looking.
Pictures of makeup being grab from the internet.. Examples: eyes or lips.

```html
<!DOCTYPE html>
<html lang="en">
<head>
<meta charset="UTF-8">
<title>Delia Marsh – Makeup Artist Business Card</title>
<link rel="stylesheet" href="https://fonts.googleapis.com/css2?family=Smythe&display=swap">
<style>
  :root {
    --page-bg: #dcdbe0;
    --card-pearl: #eeeaeb;
    --card-pearl-edge: #e2dcde;
    --accent-pink: #e63f8b;
    --band-black: #1c1a1d;
    --ink: #141214;
    --photo-violet: #8a5aa8;
    --photo-skin: #d9a58c;
    --photo-hair: #6b4a3a;
    --ornament-pink: #f2a9c9;
  }
  * { margin: 0; padding: 0; box-sizing: border-box; }
  html, body {
    width: 1067px;
    height: 1200px;
    overflow: hidden;
    background: var(--page-bg);
    font-family: "Smythe", "Georgia", serif;
  }
  .canvas {
    position: relative;
    width: 1067px;
    height: 1200px;
  }
  .card {
    position: absolute;
    left: 94px;
    width: 880px;
    height: 500px;
    border-radius: 30px;
    overflow: hidden;
    background: radial-gradient(ellipse at 60% 40%, var(--card-pearl), var(--card-pearl-edge));
    box-shadow: 0 10px 28px rgba(0, 0, 0, 0.18);
  }
  .card--front { top: 60px; }
  .card--back { top: 640px; }
  .card__art {
    position: absolute;
    inset: 0;
    width: 880px;
    height: 500px;
  }
  .front-text {
    position: absolute;
    left: 430px;
    top: 0;
    right: 20px;
    height: 100%;
  }
  .name {
    position: absolute;
    top: 28px;
    font-size: 74px;
    font-weight: 400;
    line-height: 1;
    color: var(--accent-pink);
    text-transform: uppercase;
    letter-spacing: 1px;
    white-space: nowrap;
  }
  .occupation {
    position: absolute;
    top: 100px;
    font-size: 26px;
    color: var(--ink);
    font-variant: small-caps;
    white-space: nowrap;
  }
  .phones {
    position: absolute;
    top: 222px;
    list-style: none;
    font-size: 31px;
    line-height: 48px;
    color: var(--ink);
    font-variant: small-caps;
    white-space: nowrap;
  }
  .web-contacts {
    position: absolute;
    top: 392px;
    list-style: none;
    font-size: 30px;
    line-height: 44px;
    color: var(--accent-pink);
    text-transform: uppercase;
    white-space: nowrap;
  }
  .back-website {
    position: absolute;
    left: 398px;
    top: 172px;
    font-size: 46px;
    color: var(--accent-pink);
    text-transform: uppercase;
    letter-spacing: 1px;
    white-space: nowrap;
  }
</style>
</head>
<body>
<main class="canvas">

  <section class="card card--front" aria-label="Business card, front">
    <svg class="card__art" viewBox="0 0 880 500">
      <defs>
        <clipPath id="frontCardShape">
          <rect x="0" y="0" width="880" height="500" rx="30" ry="30"/>
        </clipPath>
        <linearGradient id="portraitTones" x1="0" y1="0" x2="1" y2="1">
          <stop offset="0" stop-color="var(--photo-hair)"/>
          <stop offset="0.35" stop-color="var(--photo-skin)"/>
          <stop offset="0.6" stop-color="var(--photo-violet)"/>
          <stop offset="1" stop-color="var(--accent-pink)"/>
        </linearGradient>
        <radialGradient id="ornamentFrontTones" cx="880" cy="0" r="250" gradientUnits="userSpaceOnUse">
          <stop offset="0" stop-color="var(--accent-pink)" stop-opacity="0.55"/>
          <stop offset="1" stop-color="var(--ornament-pink)" stop-opacity="0"/>
        </radialGradient>
      </defs>
      <g clip-path="url(#frontCardShape)">
        <polygon class="portrait-area" role="img" aria-label="Close-up beauty photograph of a model wearing violet eye makeup and pink lips" points="0,0 340,0 300,250 340,500 0,500" fill="url(#portraitTones)"/>
        <polygon class="divider-band" points="340,0 374,0 334,250 374,500 340,500 300,250" fill="var(--band-black)"/>
        <polygon class="divider-stripe" points="378,0 392,0 352,250 392,500 378,500 338,250" fill="var(--accent-pink)"/>
        <rect class="floral-corner" role="img" aria-label="Pink floral vine ornament" x="630" y="0" width="250" height="250" fill="url(#ornamentFrontTones)"/>
      </g>
    </svg>
    <div class="front-text">
      <h1 class="name">Delia Marsh</h1>
      <p class="occupation">Makeup Artist</p>
      <ul class="phones">
        <li>Phone USA: +1 (415)772-0461</li>
        <li>Phone Singapore: +65 82307915</li>
      </ul>
      <ul class="web-contacts">
        <li>deliamarsh@moonveilstudio.net</li>
        <li>www.moonveilstudio.net</li>
      </ul>
    </div>
  </section>

  <section class="card card--back" aria-label="Business card, back">
    <svg class="card__art" viewBox="0 0 880 500">
      <defs>
        <clipPath id="backCardShape">
          <rect x="0" y="0" width="880" height="500" rx="30" ry="30"/>
        </clipPath>
        <linearGradient id="portraitTonesBack" x1="0" y1="0" x2="1" y2="1">
          <stop offset="0" stop-color="var(--photo-hair)"/>
          <stop offset="0.35" stop-color="var(--photo-skin)"/>
          <stop offset="0.6" stop-color="var(--photo-violet)"/>
          <stop offset="1" stop-color="var(--accent-pink)"/>
        </linearGradient>
        <radialGradient id="ornamentBackTones" cx="880" cy="0" r="320" gradientUnits="userSpaceOnUse">
          <stop offset="0" stop-color="var(--accent-pink)" stop-opacity="0.55"/>
          <stop offset="1" stop-color="var(--ornament-pink)" stop-opacity="0"/>
        </radialGradient>
      </defs>
      <g clip-path="url(#backCardShape)">
        <polygon class="portrait-area" role="img" aria-label="Close-up beauty photograph of a model wearing violet eye makeup and pink lips" points="0,0 340,0 300,250 340,500 0,500" fill="url(#portraitTonesBack)"/>
        <polygon class="divider-band" points="340,0 374,0 334,250 374,500 340,500 300,250" fill="var(--band-black)"/>
        <polygon class="divider-stripe" points="378,0 392,0 352,250 392,500 378,500 338,250" fill="var(--accent-pink)"/>
        <rect class="floral-corner" role="img" aria-label="Pink floral vine ornament" x="560" y="0" width="320" height="320" fill="url(#ornamentBackTones)"/>
      </g>
    </svg>
    <p class="back-website">www.moonveilstudio.net</p>
  </section>

</main>
</body>
</html>
```